I want ideas sample designs for my book cover

Hello,

We need a book cover designed in flat and 3D Versions. We would like to have jpg and png for final output and include a copy of the PSD for future revisions.

Here are the basic details:

Title: The Harvest of Quiet Builders
Author: Norman Quillfeather

Dimensions of book:

Was looking at the Pavo website for dimensions. I thought you may want to go on there and look at the different sizes. I used the 6x9” perfect bound US trade size for my book. You will see that this has a spine width of 0.225”, Cover size of 12.48 x 9.25” and spine begins at 6.125”

If you need background info on the author just to get an idea what he does, please check:

http://NormanQuillfeather.example

IMPORTANT: Please see attached document for a more detailed info:

Exact Title Of book
Back Cover
Spine Info
Measurements of book and dimension
Examples of book covers
Norman's photo attached

Thanks,
Darlene

Industry/Entity Type

Life Coaching

Font styles to use
Serif

Requirements
Must have
• Jpg, png and PSD files
• title
• author
• exact dimensions
• front and back cover
• flat and 3d versions

```html
<!DOCTYPE html>
<html lang="en">
<head>
<meta charset="utf-8">
<title>The Harvest of Quiet Builders – Cover Spread</title>
<link rel="stylesheet" href="https://fonts.googleapis.com/css2?family=Raleway:wght@300;400;600;700;800&family=Open+Sans:wght@400;600&display=swap">
<style>
  :root {
    --navy: #2c4577;
    --navy-deep: #1f3460;
    --magenta: #b21f6c;
    --sky-light: #eef6fb;
    --sky: #c9e3f3;
    --sky-mid: #a9d0ea;
    --paper-blue: #dbe9f1;
    --ink: #2f3a4a;
    --stage: #f4f5f7;
    --white: #ffffff;
  }
  * { box-sizing: border-box; margin: 0; padding: 0; }
  html, body { width: 1200px; height: 850px; overflow: hidden; }
  body { background: var(--stage); font-family: "Raleway", sans-serif; }

  .spread {
    position: absolute; left: 128px; top: 75px;
    width: 944px; height: 700px;
    display: flex;
    box-shadow: 0 6px 24px rgba(0,0,0,.12);
  }

  /* ---------- Back cover ---------- */
  .back-cover {
    position: relative; width: 463px; height: 100%;
    background: linear-gradient(160deg, var(--paper-blue), #eaf2f7 55%, var(--paper-blue));
  }
  .band-top { position: absolute; left: 0; right: 0; top: 0; height: 20px; background: var(--navy); }
  .band-bottom { position: absolute; left: 0; right: 0; bottom: 0; height: 24px; background: var(--magenta); }

  .author-portrait {
    position: absolute; left: 22px; top: 36px; width: 200px; height: 262px;
    background: linear-gradient(135deg, #d8d8d8, #9a9a9a 60%, #6e6e6e);
  }
  .back-author {
    position: absolute; left: 22px; top: 318px; width: 200px;
    color: var(--navy); text-transform: uppercase; line-height: 1;
  }
  .back-author .first { display: block; font-weight: 300; font-size: 26px; letter-spacing: 1px; }
  .back-author .last { display: block; font-weight: 700; font-size: 26px; letter-spacing: .5px; margin-top: 4px; }
  .author-url {
    position: absolute; left: 0; top: 388px; width: 222px; height: 28px;
    background: var(--magenta); color: var(--white);
    font-size: 10.5px; font-weight: 600; line-height: 28px; padding-left: 10px;
    white-space: nowrap; overflow: hidden;
  }
  .author-mark {
    position: absolute; left: 22px; top: 600px;
    display: flex; align-items: center; gap: 6px;
    color: var(--navy); font-weight: 600; font-size: 15px;
  }
  .author-mark .dot { width: 26px; height: 26px; border: 1.5px solid var(--navy); border-radius: 50%; }

  .back-copy {
    position: absolute; left: 238px; top: 38px; width: 206px;
    font-family: "Open Sans", sans-serif; font-size: 7.4px; line-height: 1.45;
    color: var(--ink); text-align: justify;
  }
  .back-copy p + p { margin-top: 9px; }

  /* ---------- Spine ---------- */
  .spine {
    position: relative; width: 17px; height: 100%;
    background: linear-gradient(90deg, var(--navy-deep), var(--navy), var(--navy-deep));
  }
  .spine .band-bottom { height: 24px; }
  .spine-title {
    position: absolute; top: 30px; left: 50%;
    transform-origin: 0 0; transform: rotate(90deg) translateY(-50%);
    white-space: nowrap; color: var(--white);
    font-size: 10px; font-weight: 400; letter-spacing: 1.2px; text-transform: uppercase;
  }

  /* ---------- Front cover ---------- */
  .front-cover {
    position: relative; width: 464px; height: 100%; overflow: hidden;
    background: linear-gradient(180deg, var(--sky-light) 0%, var(--sky) 35%, var(--sky-mid) 60%, var(--sky) 100%);
    text-align: center;
  }
  .title {
    position: absolute; left: 0; right: 0; top: 72px;
    text-transform: uppercase; line-height: .95;
  }
  .title .line { display: block; color: var(--navy); font-weight: 600; }
  .title .line-the { font-size: 50px; }
  .title .line-main { font-size: 44px; letter-spacing: -.5px; }
  .title .line-accent { color: var(--magenta); font-size: 42px; font-weight: 700; letter-spacing: -.5px; margin-top: 2px; }

  .subtitle {
    position: absolute; left: 34px; right: 34px; top: 250px;
    font-size: 14.5px; font-weight: 400; line-height: 1.35; color: var(--ink);
  }
  .author-band {
    position: absolute; left: 0; right: 0; top: 326px; height: 68px;
    background: linear-gradient(90deg, var(--navy-deep), var(--navy) 50%, var(--navy-deep));
    color: var(--white); text-transform: uppercase; padding-top: 11px;
  }
  .author-band .credit { display: block; font-size: 15px; font-weight: 400; letter-spacing: .3px; }
  .author-band .name { display: block; font-size: 20px; margin-top: 4px; letter-spacing: .5px; }
  .author-band .name .first { font-weight: 300; }
  .author-band .name .last { font-weight: 700; }

  .team-photo {
    position: absolute; left: 0; right: 0; top: 430px; bottom: 24px;
    background: linear-gradient(180deg, rgba(255,255,255,0), rgba(240,240,242,.9) 30%, #e6e7ea);
  }
</style>
</head>
<body>
  <main class="spread">
    <section class="back-cover">
      <div class="band-top"></div>
      <div class="author-portrait" role="img" aria-label="Black and white portrait of the author, smiling, seated in a white t-shirt"></div>
      <h2 class="back-author"><span class="first">Norman</span><span class="last">Quillfeather</span></h2>
      <div class="author-url">http://NormanQuillfeather.example</div>
      <div class="author-mark"><span class="dot"></span>NQ</div>
      <div class="back-copy">
        <p>This path goes far beyond business. It is a book for the awakening builders who are shaping companies for a better world, touching generations to come. It brings useful disruption to you and your work, turning you inside out for clear progress toward your vision, mission and values.</p>
        <p>There is a chance to live a more meaningful life by finding the quiet bond that exists between all beings. You will be moved to take your life and work to the next level when you answer the call in these pages, and to grow stronger ties with your partner, family, friends and colleagues.</p>
        <p>Norman shares heartfelt stories and insights gathered over years of travel and study. He believes that if enough people look inward, together we can make a lasting, positive mark on the world. If you are ready to take the journey within, this book is the missing link you have been looking for.</p>
        <p>Norman Quillfeather is a well known builder, speaker, mentor and best-selling author. He has guided thousands of people from many countries, and in this second book he invites you to examine the core of your true nature. Many leaders report that Norman's gift is to blend purpose with profit in a way that brings greater meaning to their work.</p>
      </div>
      <div class="band-bottom"></div>
    </section>

    <section class="spine">
      <span class="spine-title">The Harvest of Quiet Builders</span>
      <div class="band-bottom"></div>
    </section>

    <section class="front-cover">
      <div class="band-top"></div>
      <h1 class="title">
        <span class="line line-the">The</span>
        <span class="line line-main">Harvest of</span>
        <span class="line line-accent">Quiet Builders</span>
      </h1>
      <p class="subtitle">How this ancient wisdom is helping billionaires, industry icons and entrepreneurs to be better leaders, increase impact and leave a legacy.</p>
      <div class="author-band">
        <span class="credit">From the best selling author of "Stillwater"</span>
        <span class="name"><span class="first">Norman</span> <span class="last">Quillfeather</span></span>
      </div>
      <div class="team-photo" role="img" aria-label="Group photo of five business people standing with arms crossed"></div>
      <div class="band-bottom"></div>
    </section>
  </main>
</body>
</html>
```